Consulting business card

*1) An Overview:* The business is simply a financial transaction wherein I
offer to provide advice to financial holders of commercial real estate
mortgages (which are sub-performing or non-performing), and said holders
are desirous of selling said mortgages which I will offer advice to said
holders in the purchase of said mortgages. Please note the attached copy
of a proposed line-by-line business card which starts with the 1st line
"RKW Advisory, LLC" with the 2nd line "Purchase of Commercial Mortgage
Loan" and the 3rd line "Sub-performing and Non-performing" is my desired
copy subject to any suggested changes. Please ignore the the copy below
the aforementioned proposed card/copy as it will be activated at a later
date.and advise
*2) The Target Market:* I contact and advise senior officers in banks,
insurance companies, and financial institutions such as CEOs, CFOs, COOs,
and Loan Mitigation Officers: the senior officers are tasked with the
removal of sub-performing and non-performing commercial real estate loans
from their real estate portfolios. The desired market is targeted at $1-10
million USD and located in the US.
*3) Design Specifics: *STYLE should be conservative and be representative
of the financial market contacts; COLOR might show a rich forest green
element, a gold foil accent, and subtle black printing, however,
alternatively, silver foil accent(s) with strong black print would seem in
harmony with the services offered, however, I would appreciate any artful
suggestions; IMAGERY should be subtle (no logo can be strong enough to make
an immediate impact): the quality should make the recipient feel he/she has
just met an experienced and competent financial adviser (I have over 55
years of successful financial and business experience).
720.217.6154davidfredrickjones@gmail.com

```html
<!DOCTYPE html>
<html lang="en">
<head>
<meta charset="utf-8">
<title>RKW Advisory LLC – Business Card</title>
<link href="https://fonts.googleapis.com/css2?family=Courier+Prime&family=Tinos&family=Noto+Sans&display=swap" rel="stylesheet">
<style>
  :root {
    --backdrop: #3b3b3d;
    --forest: #0c3318;
    --forest-deep: #082612;
    --gold-light: #f4df98;
    --gold: #d9b95a;
    --gold-dark: #a9842c;
    --ink-green: #0f3a1c;
    --ink-dark: #1c1c1c;
    --paper-text: #f2efe2;
  }
  html, body {
    margin: 0;
    width: 1200px;
    height: 1200px;
    overflow: hidden;
    background: var(--backdrop);
  }
  .card {
    position: absolute;
    left: 75px;
    top: 300px;
    width: 1050px;
    height: 600px;
    overflow: hidden;
    box-shadow: 0 10px 30px rgba(0,0,0,0.45);
  }
  .card-art {
    position: absolute;
    inset: 0;
  }
  .company-name {
    position: absolute;
    right: 60px;
    top: 58px;
    margin: 0;
    font-family: "Courier Prime", "Courier New", monospace;
    font-weight: 400;
    font-size: 62px;
    letter-spacing: 3px;
    color: var(--paper-text);
  }
  .tagline {
    position: absolute;
    right: 60px;
    top: 142px;
    margin: 0;
    text-align: right;
    font-family: "Tinos", "Times New Roman", serif;
    font-size: 25px;
    line-height: 30px;
    color: var(--paper-text);
  }
  .person-name {
    position: absolute;
    right: 80px;
    top: 320px;
    margin: 0;
    font-family: "Tinos", "Times New Roman", serif;
    font-size: 44px;
    color: var(--ink-green);
  }
  .contact-list {
    position: absolute;
    right: 40px;
    top: 405px;
    margin: 0;
    padding: 0;
    list-style: none;
    font-family: "Noto Sans", Arial, sans-serif;
    font-size: 21px;
    color: var(--ink-dark);
  }
  .contact-item {
    display: flex;
    justify-content: flex-end;
    align-items: center;
    gap: 18px;
    height: 40px;
    letter-spacing: 1px;
  }
  .contact-icon {
    width: 22px;
    height: 22px;
    flex: none;
  }
</style>
</head>
<body>
  <article class="card">
    <svg class="card-art" viewBox="0 0 1050 600" width="1050" height="600" aria-hidden="true">
      <defs>
        <linearGradient id="brushedGold" x1="0" y1="0" x2="1" y2="1">
          <stop offset="0" stop-color="#c9a646"/>
          <stop offset="0.35" stop-color="#e8cf7c"/>
          <stop offset="0.6" stop-color="#d4b357"/>
          <stop offset="1" stop-color="#b8953a"/>
        </linearGradient>
        <linearGradient id="ribbonGold" x1="0" y1="0" x2="1" y2="0">
          <stop offset="0" stop-color="var(--gold-dark)"/>
          <stop offset="0.3" stop-color="var(--gold-light)"/>
          <stop offset="0.55" stop-color="var(--gold)"/>
          <stop offset="0.8" stop-color="var(--gold-light)"/>
          <stop offset="1" stop-color="var(--gold-dark)"/>
        </linearGradient>
        <linearGradient id="forestShade" x1="0" y1="0" x2="0" y2="1">
          <stop offset="0" stop-color="var(--forest-deep)"/>
          <stop offset="1" stop-color="var(--forest)"/>
        </linearGradient>
      </defs>
      <rect class="gold-field" width="1050" height="600" fill="url(#brushedGold)"/>
      <path class="forest-field" d="M0,0 H1050 V250 C860,250 760,262 600,330 S220,440 0,440 Z" fill="url(#forestShade)"/>
      <path class="ribbon-shadow" d="M0,452 C220,452 440,400 600,340 S860,262 1050,262" fill="none" stroke="#8a6a22" stroke-width="6" opacity="0.6"/>
      <path class="gold-ribbon" d="M0,444 C220,444 440,392 600,332 S860,254 1050,254" fill="none" stroke="url(#ribbonGold)" stroke-width="16"/>
      <path class="ribbon-highlight" d="M0,438 C220,438 440,386 600,326 S860,248 1050,248" fill="none" stroke="#fff3c4" stroke-width="2" opacity="0.8"/>
    </svg>

    <h1 class="company-name">RKW Advisory LLC</h1>
    <p class="tagline">Purchase of Commercial Mortgage Loan<br>Sub-performing and Non-performing</p>

    <p class="person-name">Tomas Heraldwick</p>
    <ul class="contact-list">
      <li class="contact-item">
        <span>555.304.8827</span>
        <svg class="contact-icon" viewBox="0 0 22 22" aria-label="Phone">
          <rect width="22" height="22" rx="2" fill="var(--ink-green)"/>
          <path d="M5 9 Q11 4 17 9 L15 11 Q11 8 7 11 Z" fill="var(--gold-light)"/>
          <rect x="6" y="11" width="10" height="6" rx="1" fill="var(--gold-light)"/>
        </svg>
      </li>
      <li class="contact-item">
        <span>tomasheraldwick@mailbox.example</span>
        <svg class="contact-icon" viewBox="0 0 22 22" aria-label="Email">
          <rect width="22" height="22" rx="2" fill="var(--ink-green)"/>
          <rect x="4" y="6" width="14" height="10" fill="var(--gold-light)"/>
          <path d="M4 6 L11 12 L18 6" fill="none" stroke="var(--ink-green)" stroke-width="1.5"/>
        </svg>
      </li>
    </ul>
  </article>
</body>
</html>
```